Ward Compass Business Card Design*

We need a business card design for our company Ward Compass. Our company is specialized in providing online consulting services regarding medical institutions, hospitals and doctors. We work with patients worldwide looking to choose between healthcare providers. We have a website you may use as a reference, where we list doctors and clinics worldwide. So we target Medical providers as well as patients worldwide.
Target Market(s)
Medical Providers and patients around the world
Industry/Entity Type
Medical
Contact Information for Business Card
Salwa Kettani
CEO
+90 612 348 2175
info@wardcompass.example
www.wardcompass.example
14 Annakhil 7 H.R.B. Rabat, Morocco
Requirements
Must have
- Company logo/name on one full side, personal info and smaller logo and company name on the other side.
Nice to have
- Smart and elegant design

```html
<!DOCTYPE html>
<html lang="en">
<head>
<meta charset="utf-8">
<title>Ward Compass Business Card</title>
<link rel="stylesheet" href="https://fonts.googleapis.com/css2?family=Montserrat:wght@300;400;700;800&family=Roboto:wght@300;400&display=swap">
<style>
  :root {
    --navy: #14375f;
    --grey: #7b7b7b;
    --rule-grey: #8a8a8a;
    --paper: #ffffff;
    --backdrop: #e9eaec;
    --ink: #2b2b2b;
  }
  * { box-sizing: border-box; margin: 0; padding: 0; }
  html, body { width: 1200px; height: 900px; overflow: hidden; }
  body {
    background: var(--backdrop);
    font-family: "Roboto", Arial, sans-serif;
    position: relative;
  }
  .card {
    position: absolute;
    left: 250px;
    width: 700px;
    height: 400px;
    background: var(--paper);
    box-shadow: 0 6px 18px rgba(0,0,0,0.10);
    overflow: hidden;
  }
  .card--front { top: 35px; }
  .card--back { top: 465px; }

  /* Front side */
  .front-band {
    position: absolute;
    top: 0; right: 0;
    width: 180px; height: 100%;
    background: var(--navy);
    border-left: 6px solid var(--rule-grey);
    display: flex; align-items: center; justify-content: center;
  }
  .front-band__url {
    writing-mode: vertical-rl;
    color: var(--paper);
    font-family: "Montserrat", sans-serif;
    font-weight: 300;
    font-size: 17px;
    letter-spacing: 4px;
  }
  .front-brand {
    position: absolute;
    left: 70px; top: 0;
    width: 444px; height: 100%;
    display: flex; align-items: center; justify-content: center;
    gap: 16px;
  }
  .brand-dot {
    width: 46px; height: 46px;
    border-radius: 50%;
    background: var(--navy);
    flex: none;
  }
  .brand-name {
    font-family: "Montserrat", sans-serif;
    font-weight: 700;
    font-size: 34px;
    color: var(--navy);
    letter-spacing: 1px;
    white-space: nowrap;
  }

  /* Back side */
  .back-band {
    position: absolute;
    top: 0; left: 0;
    width: 230px; height: 100%;
    background: var(--navy);
    border-right: 6px solid var(--rule-grey);
    display: flex; flex-direction: column; align-items: center; justify-content: center;
    gap: 18px;
  }
  .back-band__name {
    writing-mode: vertical-rl;
    transform: rotate(180deg);
    font-family: "Montserrat", sans-serif;
    font-weight: 700;
    font-size: 30px;
    color: var(--paper);
    letter-spacing: 1px;
    white-space: nowrap;
  }
  .back-band__dot {
    width: 40px; height: 40px;
    border-radius: 50%;
    background: var(--paper);
  }
  .person {
    position: absolute;
    left: 280px; top: 40px;
    right: 30px;
  }
  .person__name {
    font-family: "Montserrat", sans-serif;
    font-weight: 800;
    font-size: 38px;
    line-height: 1.05;
    white-space: nowrap;
  }
  .person__first { color: var(--navy); }
  .person__last { color: var(--grey); }
  .person__role {
    font-family: "Montserrat", sans-serif;
    font-weight: 300;
    font-size: 24px;
    color: var(--navy);
    margin-top: 2px;
  }
  .rule {
    width: 56px; height: 3px;
    background: var(--navy);
    margin: 16px 0 14px;
  }
  .address {
    font-size: 19px;
    font-weight: 300;
    color: var(--ink);
    line-height: 1.3;
  }
  .contacts { list-style: none; }
  .contacts__item {
    display: flex; align-items: center; gap: 14px;
    font-size: 19px;
    font-weight: 300;
    color: var(--ink);
    height: 32px;
  }
  .contacts__icon { width: 22px; height: 22px; flex: none; }
</style>
</head>
<body>

<section class="card card--front" aria-label="Business card front">
  <div class="front-brand">
    <span class="brand-dot"></span>
    <span class="brand-name">WARD COMPASS</span>
  </div>
  <div class="front-band">
    <span class="front-band__url">www.wardcompass.example</span>
  </div>
</section>

<section class="card card--back" aria-label="Business card back">
  <div class="back-band">
    <span class="back-band__name">WARD COMPASS</span>
    <span class="back-band__dot"></span>
  </div>

  <div class="person">
    <h1 class="person__name"><span class="person__first">Salwa</span> <span class="person__last">Kettani</span></h1>
    <p class="person__role">CEO</p>
    <div class="rule"></div>
    <p class="address">14 Annakhil<br>7 H.R.B. Rabat, Morocco</p>
    <div class="rule"></div>
    <ul class="contacts">
      <li class="contacts__item">
        <svg class="contacts__icon" viewBox="0 0 24 24" aria-hidden="true">
          <path fill="#14375f" d="M6.6 10.8a15 15 0 0 0 6.6 6.6l2.2-2.2a1 1 0 0 1 1-.25 11.4 11.4 0 0 0 3.6.57 1 1 0 0 1 1 1V20a1 1 0 0 1-1 1A17 17 0 0 1 3 4a1 1 0 0 1 1-1h3.5a1 1 0 0 1 1 1c0 1.25.2 2.45.57 3.57a1 1 0 0 1-.25 1z"/>
        </svg>
        <span>+90 612 348 2175</span>
      </li>
      <li class="contacts__item">
        <svg class="contacts__icon" viewBox="0 0 24 24" aria-hidden="true">
          <rect x="2" y="5" width="20" height="14" fill="#14375f"/>
          <path d="M2.5 5.5 12 13l9.5-7.5" fill="none" stroke="#fff" stroke-width="1.4"/>
        </svg>
        <span>info@wardcompass.example</span>
      </li>
      <li class="contacts__item">
        <svg class="contacts__icon" viewBox="0 0 24 24" aria-hidden="true">
          <circle cx="12" cy="12" r="10" fill="#14375f"/>
          <g fill="none" stroke="#fff" stroke-width="1.1">
            <ellipse cx="12" cy="12" rx="4.2" ry="10"/>
            <path d="M2 12h20M4 7h16M4 17h16"/>
          </g>
        </svg>
        <span>www.wardcompass.example</span>
      </li>
    </ul>
  </div>
</section>

</body>
</html>
```